Brightway Haus Inc. Business Card Design

Brightway Haus Inc. is in search of a great clean design for our business cards!

Looking to incorporate our full logo and watermark on side one (however, I am open to having the text and watermark separated within the design.)

On side two, I am looking to have contact information (Name, Position, Phone #, Email, Website (www.thebrightwayhaus.ca). Can have the logo and/or watermark as part of the design if applicable.

Please add tagline "Where Shine Counts" on either side 1 or 2. This tagline can be in a sans serif, serif or cursive font as long as it compliments overall design. Capitalization can be title or sentence case depending on how it fits within the design.

Get creative!! Looking for a clean, crisp, premium design! Looking for a glossy card finish with spot UV features when printed. Cards will also be printed with rounded corners. Standard dimensions (3.5 x 2).

Target Market(s)

B2B - primary clients are business owners or property management corporations. (residential jobs are few and far between)

Industry/Entity Type

Business

Contact Information for Business Card

- clean, crisp design
- double sided
- spot UV accents and glossy finish upon printing
- standard business card size (3.5 x 2) with rounded corners
- please see project description for requirements per side

Font styles to use
Sans Serif

Requirements
Must have
• - adequate bleeds with print ready files
• - cohesive design elements between side 1 & 2
• - spot UV elements (can be on both sides or just one, use your discretion)
• - colour pallet should match the logo file provided
• - incorporate tagline "where shine counts" (this tagline can be in a serif or sans serif font as long as it is complimentary to the overall design.
Nice to have
• - Premium elements with a clean design
Should not have
• - Please omit cartoon or whimsical like designs, think premium.
• - Colours should not stray from the pallet of the provided logo.

```html
<!DOCTYPE html>
<html lang="en">
<head>
<meta charset="utf-8">
<title>Brightway Haus Inc. Business Card</title>
<link rel="stylesheet" href="https://fonts.googleapis.com/css2?family=Source+Sans+3:wght@400;600;700&display=swap">
<style>
  :root {
    --navy: #1a2251;
    --teal: #10b8b9;
    --white: #ffffff;
    --silver: #c9ccd3;
    --backdrop: #e9eaec;
  }
  html, body {
    margin: 0;
    width: 1200px;
    height: 960px;
    overflow: hidden;
    background: var(--backdrop);
    font-family: "Source Sans 3", sans-serif;
  }
  .card {
    position: absolute;
    width: 600px;
    height: 343px;
    border-radius: 22px;
    overflow: hidden;
  }
  .card-front { left: 314px; top: 113px; background: var(--white); }
  .card-back { left: 311px; top: 473px; background: var(--navy); }
  .front-waves { position: absolute; inset: 0; }

  .brand {
    position: absolute;
    display: flex;
    align-items: center;
    gap: 10px;
    font-weight: 700;
    letter-spacing: 0.5px;
    white-space: nowrap;
  }
  .brand-mark { display: block; }
  .brand-front { left: 34px; top: 72px; font-size: 30px; color: var(--navy); }
  .brand-front .brand-mark { width: 26px; height: 26px; background: var(--teal); }
  .brand-back { left: 0; right: 0; top: 144px; justify-content: center; font-size: 40px; color: var(--silver); }
  .brand-back .brand-mark { width: 34px; height: 34px; background: var(--silver); }

  .person { position: absolute; left: 34px; top: 134px; }
  .person-name { margin: 0; font-size: 17px; font-weight: 600; color: var(--teal); letter-spacing: 0.3px; }
  .person-role { margin: 2px 0 0; font-size: 17px; color: var(--navy); }

  .contact {
    position: absolute;
    right: 16px;
    top: 190px;
    color: var(--white);
    font-size: 14.5px;
    text-align: right;
    line-height: 19px;
  }
  .address { margin: 0 0 10px; }
  .contact-list { list-style: none; margin: 0; padding: 0; }
  .contact-list li { display: flex; justify-content: flex-end; align-items: center; gap: 6px; }
  .contact-list svg { width: 12px; height: 12px; fill: var(--white); }

  .tagline {
    position: absolute;
    left: 100px;
    right: 100px;
    top: 274px;
    display: flex;
    align-items: center;
    gap: 2px;
    color: var(--white);
    font-size: 18px;
    font-weight: 600;
    white-space: nowrap;
  }
  .tagline-rule { flex: 1; height: 1px; }
  .tagline-rule.left { background: linear-gradient(to right, transparent, var(--white)); }
  .tagline-rule.right { background: linear-gradient(to left, transparent, var(--white)); }
</style>
</head>
<body>
  <section class="card card-front">
    <svg class="front-waves" viewBox="0 0 600 343" aria-hidden="true">
      <path d="M0,278 C120,312 250,300 360,222 C470,140 540,62 600,16 L600,343 L0,343 Z" fill="var(--teal)"/>
      <path d="M0,278 C120,312 250,300 360,222 C470,140 540,62 600,16" fill="none" stroke="var(--white)" stroke-width="3"/>
      <path d="M130,296 C260,292 360,214 462,118 C515,66 550,26 568,0 L600,0 L600,12 C540,58 468,136 356,218 C280,272 210,296 130,296 Z" fill="var(--navy)"/>
    </svg>
    <div class="brand brand-front"><span class="brand-mark"></span>BRIGHTWAY HAUS INC.</div>
    <div class="person">
      <p class="person-name">MARLEN OSTROVA</p>
      <p class="person-role">CEO/FOUNDER</p>
    </div>
    <div class="contact">
      <p class="address">4120 Larkspur Row<br>Halden, Ontario 52180</p>
      <ul class="contact-list">
        <li>512 604 7731 <svg viewBox="0 0 12 12"><path d="M1,4 Q6,0 11,4 L10,6 L8,5 L8,4 Q6,3 4,4 L4,5 L2,6 Z M2,7 L10,7 L11,11 L1,11 Z"/></svg></li>
        <li>512 604 7789 <svg viewBox="0 0 12 12"><path d="M3,0 H9 V12 H3 Z M4,1.5 V9 H8 V1.5 Z"/></svg></li>
        <li>512 604 7702 <svg viewBox="0 0 12 12"><path d="M3,0 H9 V4 H3 Z M0,5 H12 V10 H10 V8 H2 V10 H0 Z M3,9 H9 V12 H3 Z"/></svg></li>
        <li>hello@brightway.ca <svg viewBox="0 0 12 12"><path d="M0,2 H12 L6,7 Z M0,3.5 L6,8.5 L12,3.5 V10 H0 Z"/></svg></li>
        <li>www.thebrightwayhaus.ca <svg viewBox="0 0 12 12"><circle cx="6" cy="6" r="6"/></svg></li>
      </ul>
    </div>
  </section>

  <section class="card card-back">
    <div class="brand brand-back"><span class="brand-mark"></span>BRIGHTWAY HAUS INC.</div>
    <div class="tagline">
      <span class="tagline-rule left"></span>Where Shine Counts<span class="tagline-rule right"></span>
    </div>
  </section>
</body>
</html>
```